TWPC Business Card Design

Business card for sole operator professional civil and traffic engineer.
Clients are developers and planners who require assistance with traffic strategic master planning advice and design development for access and infrastructure associated with the development.
Colours already in use are greens for the business name and black for other legend. The attached file shows the letterhead template which is currently in use.
Target Market(s)
Professional Clients in development industry
Most clients known to the Principal and card is mostly required to allow ongoing contact
Industry/Entity Type
Business
Contact Information for Business Card
LACHLAN PETTIGREW CONSULTING PARTNERS
ABN 37 814 529 106
PO Box 418 KELWOOD NSW 2619
Lachlan Pettigrew 0412 358 971
l.pettigrew@corvanmail.net

```html
<!DOCTYPE html>
<html lang="en">
<head>
<meta charset="utf-8">
<title>TWPC Business Card Design</title>
<link rel="stylesheet" href="https://fonts.googleapis.com/css2?family=Montserrat:wght@400;500;600;700&family=Didact+Gothic&display=swap">
<style>
  :root {
    --green: #8cc63f;
    --green-deep: #5fae3a;
    --green-pale: #cbe9bb;
    --ink: #0c0c0c;
    --ink-soft: #1c1c1c;
    --paper: #ffffff;
    --text-light: #f2f2f2;
    --label: #111111;
  }
  * { box-sizing: border-box; margin: 0; padding: 0; }
  html, body { width: 1200px; height: 354px; overflow: hidden; background: var(--paper); }
  body { position: relative; font-family: "Montserrat", sans-serif; }

  .card {
    position: absolute; top: 22px; width: 280px; height: 165px;
    border-radius: 12px; overflow: hidden;
    background: radial-gradient(circle at 45% 40%, var(--ink-soft), var(--ink) 75%);
  }
  .card--one-front { left: 6px; }
  .card--one-back { left: 296px; }
  .card--two-front { left: 624px; }
  .card--two-back { left: 914px; background: linear-gradient(135deg, var(--green-pale), #e3f3da); }

  .card__accent { position: absolute; inset: 0; width: 100%; height: 100%; }

  .brand { position: absolute; color: var(--green); font-weight: 600; }
  .brand__mark { display: block; line-height: 1; letter-spacing: 0.5px; }
  .brand__name { display: block; text-transform: uppercase; }

  .card__front-brand { left: 22px; top: 56px; }
  .card__front-brand .brand__mark { font-size: 31px; }
  .card__front-brand .brand__name { font-size: 6px; letter-spacing: 0.6px; margin-top: 4px; line-height: 1.35; }

  .card__divider { position: absolute; left: 122px; top: 38px; width: 1px; height: 92px; background: var(--green); }

  .contact { position: absolute; left: 133px; top: 50px; list-style: none; color: var(--text-light); font-size: 7px; }
  .contact__person { color: var(--green); font-weight: 700; font-size: 8.5px; letter-spacing: 0.6px; margin-bottom: 6px; }
  .contact__line { display: flex; align-items: center; gap: 4px; margin-bottom: 5px; }
  .contact__line svg { width: 7px; height: 7px; fill: var(--green); flex: none; }
  .contact__abn { margin-top: 9px; padding-left: 40px; }

  .card__back-brand { left: 0; right: 0; top: 36px; text-align: center; }
  .card__back-brand .brand__mark { font-size: 62px; }
  .card__back-brand .brand__name { font-size: 9px; letter-spacing: 2px; margin-top: 6px; line-height: 1.4; }
  .card--two-back .brand { color: var(--green-deep); }

  .showcase-logo { left: 0; right: 0; top: 200px; text-align: center; }
  .showcase-logo .brand__mark { font-size: 92px; }
  .showcase-logo .brand__name { font-size: 20px; letter-spacing: 1.5px; margin-top: 8px; }

  .example-label { position: absolute; top: 296px; font-family: "Didact Gothic", sans-serif; font-size: 34px; color: var(--label); }
  .example-label--one { left: 106px; }
  .example-label--two { left: 816px; }
</style>
</head>
<body>

<!-- Example 1 -->
<section class="card card--one-front">
  <svg class="card__accent" viewBox="0 0 280 165" aria-hidden="true">
    <polygon points="0,0 62,0 14,34 14,131 62,165 0,165" fill="var(--green)"/>
  </svg>
  <div class="brand card__front-brand">
    <span class="brand__mark">TWPC</span>
    <span class="brand__name">Lachlan Pettigrew<br>Consulting Partners</span>
  </div>
  <div class="card__divider"></div>
  <ul class="contact">
    <li class="contact__person">LACHLAN PETTIGREW</li>
    <li class="contact__line"><svg viewBox="0 0 10 10"><path d="M5 0a3.5 3.5 0 0 0-3.5 3.5C1.5 6 5 10 5 10s3.5-4 3.5-6.5A3.5 3.5 0 0 0 5 0zm0 5a1.5 1.5 0 1 1 0-3 1.5 1.5 0 0 1 0 3z"/></svg>PO Box 418 KELWOOD NSW 2619</li>
    <li class="contact__line"><svg viewBox="0 0 10 10"><path d="M2 0l2 2.5-1 1.2a6 6 0 0 0 3.3 3.3l1.2-1L10 8l-1 2C4 10 0 6 0 1z"/></svg>0412 358 971</li>
    <li class="contact__line"><svg viewBox="0 0 10 10"><path d="M0 2h10v6H0zM0 2l5 3.5L10 2" stroke="var(--ink)" stroke-width="0.8"/></svg>l.pettigrew@corvanmail.net</li>
    <li class="contact__abn">ABN 37 814 529 106</li>
  </ul>
</section>

<section class="card card--one-back">
  <svg class="card__accent" viewBox="0 0 280 165" aria-hidden="true">
    <polygon points="40,140 280,126 280,132 40,146" fill="var(--green)"/>
  </svg>
  <div class="brand card__back-brand">
    <span class="brand__mark">TWPC</span>
    <span class="brand__name">Lachlan Pettigrew<br>Consulting Partners</span>
  </div>
</section>

<!-- Example 2 -->
<section class="card card--two-front">
  <svg class="card__accent" viewBox="0 0 280 165" aria-hidden="true">
    <polygon points="0,0 80,0 0,30" fill="var(--green)"/>
    <polygon points="280,165 200,165 280,135" fill="var(--green)"/>
  </svg>
  <div class="brand card__front-brand">
    <span class="brand__mark">TWPC</span>
    <span class="brand__name">Lachlan Pettigrew<br>Consulting Partners</span>
  </div>
  <div class="card__divider"></div>
  <ul class="contact">
    <li class="contact__person">LACHLAN PETTIGREW</li>
    <li class="contact__line"><svg viewBox="0 0 10 10"><path d="M5 0a3.5 3.5 0 0 0-3.5 3.5C1.5 6 5 10 5 10s3.5-4 3.5-6.5A3.5 3.5 0 0 0 5 0zm0 5a1.5 1.5 0 1 1 0-3 1.5 1.5 0 0 1 0 3z"/></svg>PO Box 418 KELWOOD NSW 2619</li>
    <li class="contact__line"><svg viewBox="0 0 10 10"><path d="M2 0l2 2.5-1 1.2a6 6 0 0 0 3.3 3.3l1.2-1L10 8l-1 2C4 10 0 6 0 1z"/></svg>0412 358 971</li>
    <li class="contact__line"><svg viewBox="0 0 10 10"><path d="M0 2h10v6H0zM0 2l5 3.5L10 2" stroke="var(--ink)" stroke-width="0.8"/></svg>l.pettigrew@corvanmail.net</li>
    <li class="contact__abn">ABN 37 814 529 106</li>
  </ul>
</section>

<section class="card card--two-back">
  <div class="brand card__back-brand">
    <span class="brand__mark">TWPC</span>
    <span class="brand__name">Lachlan Pettigrew<br>Consulting Partners</span>
  </div>
</section>

<!-- Central logo -->
<div class="brand showcase-logo">
  <span class="brand__mark">TWPC</span>
  <span class="brand__name">Lachlan Pettigrew</span>
</div>

<p class="example-label example-label--one">Example 1</p>
<p class="example-label example-label--two">Example 2</p>

</body>
</html>
```